KVR Inc Web Design

WHAT ARE WE DOING?
We are developing a new website look and feel for a new company called KVR Inc. This new look and feel should include colors, design elements, choice of photography and other imagery, fonts, and other user experience elements.

WHAT DO THEY DO?
KVR, Inc, makes tools for researchers who are studying protein-protein interactions. These molecules are the basic tools of biology, and serve as key targets for drug developers and disease researchers. The world of proteins is enormously complex, and companies like KVR provide researchers with critical tools that help them elucidate this world.

WHO ARE WE TALKING TO?
The target audience for this website are professional scientists working in university research or biopharma drug development. They are highly sophisticated consumers looking for key tools that will advance their research.

WHAT DO WE WANT THEM TO DO?
The site is an information resource for the customer exploring the tools that KVR sells and the scientific issues surrounding protein-protein interactions. They should be able to navigate easily to their content of choice, while the whole site should convey a professionalism that enhanced KVR’s credibility.

WHAT DOES THE KVR BRAND STAND FOR?
KVR stands for illumination. Proteins are challenging to study, and KVR exists to help shed light on their workings.

WHAT ARE THE KEY VALUES OF THE KVR BRAND?
Integrity. Innovation. Insight.

WHAT ARE THE EXECUTIONAL MANDITORIES?
The look and feel is completely up for grabs. Nothing is off the table.

WHAT ARE THE DELIVERABLES?
We need new designs for the following templates:
http://cms.marlowbench.com/
http://cms.marlowbench.com/products-and-services/instruments-3/bench-top-instruments/
http://cms.marlowbench.com/category/lab-study/

```html
<!DOCTYPE html>
<html lang="en">
<head>
<meta charset="utf-8">
<title>KVR Inc — Pipettes</title>
<link rel="stylesheet" href="https://fonts.googleapis.com/css2?family=Figtree:wght@400;500;600;700&display=swap">
<style>
:root{
  --accent:#f7a62b;
  --ink:#111;
  --nav:#6a6a6a;
  --body:#707070;
  --rule:#cfcfcf;
  --search:#8a8a8a;
  --active:#33b2d6;
  --tab:#e9e8e8;
  --footer:#6e6e6e;
  --footer-text:#fff;
}
*{box-sizing:border-box;margin:0;padding:0}
html,body{width:1200px;height:1178px;overflow:hidden;background:#fff}
body{font-family:"Figtree",sans-serif;position:relative;color:var(--body)}
.topbar{position:absolute;left:0;top:0;width:1200px;height:3px;background:var(--accent)}
.header{position:absolute;left:0;top:3px;width:1200px;height:58px;border-bottom:1px solid #e6e6e6;box-shadow:0 1px 3px rgba(0,0,0,.05)}
.brand{position:absolute;left:120px;top:12px;font-size:30px;font-weight:400;letter-spacing:9px;color:#7a7a7a;line-height:32px}
.main-nav{position:absolute;top:18px;left:0;display:flex}
.main-nav a{position:absolute;white-space:nowrap;font-size:16px;font-weight:600;color:var(--nav);text-decoration:none}
.main-nav a.current{color:var(--accent)}
.search{position:absolute;left:942px;top:16px;width:138px;height:24px;background:var(--search);border-radius:2px;color:#e4e4e4;font-size:13px;line-height:24px;padding-left:8px}
.search svg{position:absolute;right:6px;top:5px}
.page-title{position:absolute;left:120px;top:92px;font-size:27px;font-weight:400;color:var(--ink);letter-spacing:.3px}
.select{position:absolute;left:886px;top:97px;width:194px;height:24px;background:#8d8d8d;color:#f0f0f0;font-size:13px;line-height:24px;padding-left:15px}
.select svg{position:absolute;right:10px;top:9px}
.rule{position:absolute;left:120px;top:130px;width:961px;height:4px;border-top:1px solid var(--rule);border-bottom:1px solid var(--rule)}
.lead{position:absolute;left:119px;top:144px;width:970px;font-size:21.5px;line-height:27px;font-weight:400;color:var(--ink)}
.hero{position:absolute;left:120px;top:220px;width:961px;height:338px;background:linear-gradient(90deg,#5a4a3e 0%,#8a7a6c 22%,#3f78b8 45%,#3a7fd0 70%,#2f6cb8 100%)}
.copy{position:absolute;left:120px;width:955px;font-size:13.2px;line-height:18.75px;color:var(--body)}
.copy.one{top:586px}
.copy.two{top:680px}
.tabs{position:absolute;left:120px;top:820px;width:254px}
.tabs li{list-style:none;position:relative;height:46px;margin-bottom:1.6px;background:linear-gradient(90deg,#e2e1e1,#f1f0f0 50%,#e4e3e3);font-size:19px;color:var(--ink);padding-left:27px;line-height:46px}
.tabs li.active{background:var(--active);color:#fff}
.tabs li.active svg{position:absolute;left:254px;top:0}
.feature-photo{position:absolute;left:414px;top:820px;width:311px;height:241px;background:linear-gradient(135deg,#c9d2da,#eef0f1 45%,#9fb4c8 100%)}
.feature-copy{position:absolute;left:736px;top:818px;width:345px;font-size:13.2px;line-height:18.75px;color:var(--body)}
.feature-copy strong{color:#5e5e5e;font-weight:700}
.feature-copy p+p{margin-top:18.75px}
.footer{position:absolute;left:0;top:1115px;width:1200px;height:63px;background:var(--footer)}
.footer-nav{position:absolute;left:120px;top:25px;font-size:13px;color:var(--footer-text);white-space:nowrap}
.footer-nav span{margin:0 6px}
.social{position:absolute;left:824px;top:21px;display:flex;gap:6px}
.copyright{position:absolute;left:929px;top:25px;font-size:14px;color:var(--footer-text)}
.copyright em{font-style:normal;color:var(--accent)}
</style>
</head>
<body>
<div class="topbar"></div>
<header class="header">
  <div class="brand">KVR INC</div>
  <nav class="main-nav">
    <a style="left:305px">Company</a>
    <a class="current" style="left:398px">Products &amp; Services</a>
    <a style="left:562px">Learning Center</a>
    <a style="left:699px">Events</a>
    <a style="left:771px">KVR News</a>
    <a style="left:862px">Contact</a>
  </nav>
  <div class="search">Search
    <svg width="14" height="14" viewBox="0 0 14 14"><circle cx="5.5" cy="5.5" r="4.3" fill="none" stroke="#d6d6d6" stroke-width="1.6"/><line x1="8.6" y1="8.6" x2="13" y2="13" stroke="#d6d6d6" stroke-width="1.8"/></svg>
  </div>
</header>

<h1 class="page-title">PIPETTES</h1>
<div class="select">Product Overview
  <svg width="12" height="7" viewBox="0 0 12 7"><path d="M0 0H12L6 7Z" fill="#dcdcdc"/></svg>
</div>
<div class="rule"></div>
<p class="lead">Donec non massa lacinia, commodo eros eget, rutrum arcu. Integer tincidunt, velit id eleifend congue, odio massa consequat mauris, massa consequat</p>

<div class="hero" role="img" aria-label="Researcher in protective mask and goggles using a pipette against a blue background"></div>

<p class="copy one">Quisque feugiat lacus vitae posuere blandit. Nulla sit amet laoreet felis, id rhoncus nisl. Aenean fringilla quam in nibh egestas, in malesuada tortor accumsan. Donec non massa lacinia, commodo eros eget, rutrum arcu. Integer tincidunt, velit id eleifend congue, odio massa consequat mauris, a scelerisque nulla nulla eu nulla. Cras luctus pulvinar nibh ut viverra. Aenean vestibulum vitae justo non dictum. Mauris ut tellus in dui pretium dictum nec non tortor. Nulla a velit quis dolor interdum scelerisque eu et nisl.</p>
<p class="copy two">Donec auctor mollis ligula eget molestie. Aliquam erat volutpat. Curabitur sapien libero, condimentum ac nisl nec, ultricies tincidunt ipsum. Donec in iaculis metus. Mauris eleifend nisi non sapien commodo, hendrerit ornare lacus consectetur. Pellentesque faucibus, purus non dictum lacinia, ante augue pretium neque, vitae egestas dui nisl et enim. Suspendisse iaculis nibh vel lacinia rhoncus Donec auctor mollis ligula eget molestie. Aliquam erat volutpat. Curabitur sapien libero, condimentum ac nisl nec, ultricies tincidunt ipsum. Donec in iaculis metus. Mauris eleifend nisi non sapien commodo, hendrerit ornare lacus consectetur. Pellentesque faucibus, purus non dictum lacinia, ante augue pretium neque, vitae egestas dui nisl et enim.</p>

<ul class="tabs">
  <li>Overview</li>
  <li class="active">Features<svg width="16" height="46" viewBox="0 0 16 46"><path d="M0 0L16 23L0 46Z" fill="#33b2d6"/></svg></li>
  <li>Specifications</li>
  <li>FAQ's</li>
  <li>Manuals</li>
</ul>

<div class="feature-photo" role="img" aria-label="Two lab scientists in white coats and goggles examining a plant seedling in a test tube"></div>
<div class="feature-copy">
  <p><strong>Quisque feugiat lacus vitae posuere blandit. Nulla sit amet laoreet felis, id rhoncus nisl. Aenean fringilla</strong> quam in nibh egestas, in malesuada tortor accumsan. Donec non massa lacinia, commodo eros eget, rutrum arcu. Integer tincidunt, velit id eleifend congue, odio massa consequat mauris, a scelerisque nulla nulla eu nulla. Cras luctus pulvinar nibh ut viverra. Aenean vestibulum vitae justo non dictum. Mauris ut tellus in dui pretium dictum nec non tortor.</p>
  <p>Nulla a velit quis dolor interdum scelerisque eu et nisl. Donec auctor mollis ligula eget molestie. Aliquam erat volutpat. Curabitur sapien libero</p>
</div>

<footer class="footer">
  <div class="footer-nav">Company<span>-</span>Products &amp; Services<span>-</span>Learning Center<span>-</span>Events<span>-</span>KVR News<span>-</span>Contact</div>
  <div class="social" aria-label="Social links">
    <svg width="24" height="24" viewBox="0 0 24 24"><circle cx="12" cy="12" r="12" fill="#fff"/></svg>
    <svg width="24" height="24" viewBox="0 0 24 24"><circle cx="12" cy="12" r="12" fill="#fff"/></svg>
    <svg width="24" height="24" viewBox="0 0 24 24"><circle cx="12" cy="12" r="12" fill="#fff"/></svg>
  </div>
  <div class="copyright">Copyright © <em>KVR Inc.</em> 2013</div>
</footer>
</body>
</html>
```